3D abstract logo Construction, Kitchen and Bath design and Project Management Business Card Design

I want a 3d abstract logo for a new General Construction, Kitchen and Bath design and Project Management Company located at Philadelphia PA, we want to put our logo in the white color trucks too. I want to look professional and serious at the same time look like an architect design and the warm originals color that make you feel in a nice decorated home, I like the colors trend in this link:
http://www.quellmark.example/qm/ggs/pageeditor.aspx?alt_doc_id=RT41K-M9B33-2W5&doc_id=5913046628&pf_id=D4H

I was thinking about a roof and the PA font could have square shape or like wood framing with two tones of the brick color black and creamy yellow color.... Also I like the keystone Idea like the modification or the Ridgeline Parkway logo but curvy at the top

The final design should communicate big company (because we want to grow), responsible, professional and organized that really care about our customers and give them everything they need... plan and design, excellent labor and Project Management
Updates

I doesn't have to be 3d

Reason: I haven't received enough options...

Please stick with the warm tones shown in the image001 attached I like spicy cinnamon instead a cold wine or brick color and also the cream yellowish tones added

Hello designers, please use only the idea and colors of the image001 I don't want to be stick with a house logo because I do commercial construction too so I prefer work around the keystone idea maybe leaving the style of the PA.
I'd like the base tone on the card dark like first option and you can send me a white option too.

Please send me your ideas as soon as possible 

Thank you so much!

Target Market(s)

Builders, State, commercial business owners, Property owners or Real State and Property Management Companies

Industry/Entity Type

Architect

Contact Information for Business Card

RK Buildworks LLC
“Your project is our business”
Lorna Vasquel Eng.
President
Commercial & Residential General Construction
Kitchen & Bath Design | Project Management
Phone: 555-304-7718 | Fax: 555-304-7719 Cell: 555-862-3097
lorna@rkbuildworks.example

```html
<!DOCTYPE html>
<html lang="en">
<head>
<meta charset="utf-8">
<title>RK Buildworks – Business Card Colour Options</title>
<link rel="stylesheet" href="https://fonts.googleapis.com/css2?family=Arimo:ital,wght@0,400;0,700;1,400&display=swap">
<style>
  :root {
    --page-bg: #3b2c27;
    --card-cream: #f8f1dc;
    --brand-red: #8c1c1c;
    --tan-text: #c59b7a;
    --ink: #1e1a18;
    --band-cinnamon: #c4977a;
    --band-sand: #cfa07c;
    --band-gold: #dbb97c;
    --band-spice: #c48a68;
  }
  * { box-sizing: border-box; margin: 0; padding: 0; }
  html, body {
    width: 1200px; height: 961px; overflow: hidden;
    background: var(--page-bg);
    font-family: "Arimo", Arial, sans-serif;
  }
  .option-grid {
    display: grid;
    grid-template-columns: 600px 600px;
    grid-template-rows: 480px 481px;
  }
  .option-cell {
    display: flex; align-items: center; justify-content: center;
  }
  .card {
    --band: var(--band-cinnamon);
    position: relative;
    width: 500px; height: 286px;
    background: var(--card-cream);
    box-shadow: 0 10px 24px rgba(0,0,0,0.45);
    overflow: hidden;
  }
  .card--sand { --band: var(--band-sand); }
  .card--gold { --band: var(--band-gold); }
  .card--spice { --band: var(--band-spice); }
  .card__art { position: absolute; inset: 0; }
  .card__band { fill: var(--band); }
  .card__arc { fill: none; stroke: var(--brand-red); }
  .card__arc--tan { stroke: var(--tan-text); }
  .card__mark { fill: var(--brand-red); }
  .card__name {
    position: absolute; left: 32px; top: 24px;
    font-size: 26px; font-weight: 700; letter-spacing: 0.5px;
    color: var(--brand-red); text-transform: uppercase;
  }
  .card__title {
    position: absolute; left: 34px; top: 54px;
    font-size: 13px; font-style: italic; color: var(--brand-red);
  }
  .card__services {
    position: absolute; left: 34px; top: 82px;
    font-size: 15px; line-height: 18px; color: var(--tan-text);
  }
  .card__contacts {
    position: absolute; left: 38px; top: 146px;
    display: grid; grid-template-columns: 46px auto;
    row-gap: 5px; font-size: 11px;
  }
  .card__label { color: var(--tan-text); }
  .card__value { color: var(--ink); }
  .card__company {
    position: absolute; left: 402px; top: 258px; width: 100px;
    text-align: center; white-space: nowrap;
    font-size: 11px; font-weight: 700; color: var(--brand-red);
  }
</style>
</head>
<body>
<main class="option-grid">
  <section class="option-cell">
    <article class="card card--cinnamon">
      <svg class="card__art" viewBox="0 0 500 286" aria-hidden="true">
        <path class="card__band" d="M340 0 Q430 143 366 286 L500 286 L500 0 Z"/>
        <path class="card__arc" stroke-width="3" d="M300 0 Q405 140 332 286"/>
        <path class="card__arc" stroke-width="1.5" d="M316 0 Q420 140 348 286"/>
        <path class="card__arc card__arc--tan" stroke-width="2" d="M326 0 Q428 140 357 286"/>
        <circle class="card__mark" cx="452" cy="224" r="26"/>
      </svg>
      <h1 class="card__name">Lorna Vasquel</h1>
      <p class="card__title">Eng. President</p>
      <p class="card__services">Commercial &amp; Residential General<br>Construction Kitchen &amp; Bath Design</p>
      <dl class="card__contacts">
        <dt class="card__label">Phone:</dt><dd class="card__value">555-304-7718</dd>
        <dt class="card__label">Fax:</dt><dd class="card__value">555-304-7719</dd>
        <dt class="card__label">Cell:</dt><dd class="card__value">555-862-3097</dd>
        <dt class="card__label">Email:</dt><dd class="card__value">lorna@rkbuildworks.example</dd>
      </dl>
      <p class="card__company">RK Buildworks</p>
    </article>
  </section>
  <section class="option-cell">
    <article class="card card--sand">
      <svg class="card__art" viewBox="0 0 500 286" aria-hidden="true">
        <path class="card__band" d="M340 0 Q430 143 366 286 L500 286 L500 0 Z"/>
        <path class="card__arc" stroke-width="3" d="M300 0 Q405 140 332 286"/>
        <path class="card__arc" stroke-width="1.5" d="M316 0 Q420 140 348 286"/>
        <path class="card__arc card__arc--tan" stroke-width="2" d="M326 0 Q428 140 357 286"/>
        <circle class="card__mark" cx="452" cy="224" r="26"/>
      </svg>
      <h1 class="card__name">Lorna Vasquel</h1>
      <p class="card__title">Eng. President</p>
      <p class="card__services">Commercial &amp; Residential General<br>Construction Kitchen &amp; Bath Design</p>
      <dl class="card__contacts">
        <dt class="card__label">Phone:</dt><dd class="card__value">555-304-7718</dd>
        <dt class="card__label">Fax:</dt><dd class="card__value">555-304-7719</dd>
        <dt class="card__label">Cell:</dt><dd class="card__value">555-862-3097</dd>
        <dt class="card__label">Email:</dt><dd class="card__value">lorna@rkbuildworks.example</dd>
      </dl>
      <p class="card__company">RK Buildworks</p>
    </article>
  </section>
  <section class="option-cell">
    <article class="card card--gold">
      <svg class="card__art" viewBox="0 0 500 286" aria-hidden="true">
        <path class="card__band" d="M340 0 Q430 143 366 286 L500 286 L500 0 Z"/>
        <path class="card__arc" stroke-width="3" d="M300 0 Q405 140 332 286"/>
        <path class="card__arc" stroke-width="1.5" d="M316 0 Q420 140 348 286"/>
        <path class="card__arc card__arc--tan" stroke-width="2" d="M326 0 Q428 140 357 286"/>
        <circle class="card__mark" cx="452" cy="224" r="26"/>
      </svg>
      <h1 class="card__name">Lorna Vasquel</h1>
      <p class="card__title">Eng. President</p>
      <p class="card__services">Commercial &amp; Residential General<br>Construction Kitchen &amp; Bath Design</p>
      <dl class="card__contacts">
        <dt class="card__label">Phone:</dt><dd class="card__value">555-304-7718</dd>
        <dt class="card__label">Fax:</dt><dd class="card__value">555-304-7719</dd>
        <dt class="card__label">Cell:</dt><dd class="card__value">555-862-3097</dd>
        <dt class="card__label">Email:</dt><dd class="card__value">lorna@rkbuildworks.example</dd>
      </dl>
      <p class="card__company">RK Buildworks</p>
    </article>
  </section>
  <section class="option-cell">
    <article class="card card--spice">
      <svg class="card__art" viewBox="0 0 500 286" aria-hidden="true">
        <path class="card__band" d="M340 0 Q430 143 366 286 L500 286 L500 0 Z"/>
        <path class="card__arc" stroke-width="3" d="M300 0 Q405 140 332 286"/>
        <path class="card__arc" stroke-width="1.5" d="M316 0 Q420 140 348 286"/>
        <path class="card__arc card__arc--tan" stroke-width="2" d="M326 0 Q428 140 357 286"/>
        <circle class="card__mark" cx="452" cy="224" r="26"/>
      </svg>
      <h1 class="card__name">Lorna Vasquel</h1>
      <p class="card__title">Eng. President</p>
      <p class="card__services">Commercial &amp; Residential General<br>Construction Kitchen &amp; Bath Design</p>
      <dl class="card__contacts">
        <dt class="card__label">Phone:</dt><dd class="card__value">555-304-7718</dd>
        <dt class="card__label">Fax:</dt><dd class="card__value">555-304-7719</dd>
        <dt class="card__label">Cell:</dt><dd class="card__value">555-862-3097</dd>
        <dt class="card__label">Email:</dt><dd class="card__value">lorna@rkbuildworks.example</dd>
      </dl>
      <p class="card__company">RK Buildworks</p>
    </article>
  </section>
</main>
</body>
</html>
```